Building company buisness cards

We are looking for a sharp modern new look for our business cards.
We are a New Zealand based company that specialises in house and land packages.
We have attached a photo of the current logo and would like to see if it can be improved somehow if needed.
We are open to any colours but we have chosen green at this stage.
Feel free to change the font and make the logo smarter looking.
Play with the colours and see what looks best.

We want a card that looks so good know one will want to throw it away!

Target Market(s)

Home buyers

Industry/Entity Type

Building

Contact Information for Business Card

Derek Tolvane
0217394062
dtolvane@quillmarkhomesteads.co.nz
quillmarkhomesteads.co.nz

Font styles to use
Serif
Sans Serif

Colors

Designer to choose colors to be used in the design.

Requirements
Must have
• Logo and company name on one side, details on the other side
Nice to have
• Color codes for the original green are HEX #4a8028, RGB(74,128,40), CMYK(42,0,69,50)
• Round corners, Raised and/or spot UV

```html
<!DOCTYPE html>
<html lang="en">
<head>
<meta charset="utf-8">
<title>Quillmark Homesteads – Business Card</title>
<link rel="stylesheet" href="https://fonts.googleapis.com/css2?family=Roboto:wght@400;500;700&display=swap">
<style>
  :root {
    --brand-green: #4a8028;
    --card-white: #ffffff;
    --backdrop: #2b2b2b;
    --text-light: #ffffff;
  }
  * { margin: 0; padding: 0; box-sizing: border-box; }
  html, body {
    width: 1125px;
    height: 1200px;
    overflow: hidden;
    background: var(--backdrop);
    font-family: "Roboto", Arial, sans-serif;
  }
  .card {
    position: absolute;
    left: 150px;
    width: 826px;
    height: 472px;
    border-radius: 30px;
    overflow: hidden;
  }
  .card--front { top: 98px; background: var(--card-white); }
  .card--back { top: 630px; background: var(--brand-green); }

  .wordmark {
    position: absolute;
    left: 0;
    right: 0;
    text-align: center;
    font-weight: 500;
    letter-spacing: 2px;
    text-transform: uppercase;
    line-height: 1.1;
  }
  .card--front .wordmark {
    top: 72px;
    font-size: 42px;
    color: var(--brand-green);
  }
  .card--back .wordmark {
    top: 190px;
    font-size: 52px;
    color: var(--text-light);
  }

  .roof-band {
    position: absolute;
    left: 0;
    bottom: 0;
    width: 826px;
    height: 252px;
  }
  .roof-band path { fill: var(--brand-green); }

  .contact {
    position: absolute;
    left: 0;
    right: 0;
    top: 310px;
    text-align: center;
    color: var(--text-light);
  }
  .contact__name {
    font-size: 29px;
    font-weight: 700;
    letter-spacing: 0.5px;
    margin-bottom: 18px;
    text-transform: uppercase;
  }
  .contact__line {
    font-size: 19px;
    font-weight: 400;
    line-height: 26px;
  }
</style>
</head>
<body>
  <section class="card card--front">
    <h1 class="wordmark">Quillmark Homesteads.</h1>
    <svg class="roof-band" viewBox="0 0 826 252" aria-hidden="true">
      <path d="M30 252 L358 22 Q396 -4 448 8 Q468 14 488 30 L800 252 Z"/>
    </svg>
    <div class="contact">
      <p class="contact__name">Derek Tolvane</p>
      <p class="contact__line">(P) 0217394062</p>
      <p class="contact__line">dtolvane@quillmarkhomesteads.co.nz</p>
      <p class="contact__line">quillmarkhomesteads.co.nz</p>
    </div>
  </section>

  <section class="card card--back">
    <p class="wordmark">Quillmark Homesteads.</p>
  </section>
</body>
</html>
```